Our companies name is The Gilded Ladle and we specialize in craft cupcakes, what I mean by that is that we bake our cupcakes with craft beer and other alcoholic drinks. We are trying to focus on being elegant but at the same time unpretentious. Since we are incorporating beer in our cupcakes we want the business card to have our logo in the front and our information in the back.

Once we select the best design we will provide the contact information to be added. Thank you.

Industry/Entity Type

Business

Font styles to use
Decorative
Script

Requirements
Must have
• Round corners
Should not have
• Square corners

```html
<!DOCTYPE html>
<html lang="en">
<head>
<meta charset="utf-8">
<title>The Gilded Ladle — Business Card</title>
<link rel="stylesheet" href="https://fonts.googleapis.com/css2?family=Michroma&display=swap">
<style>
  :root {
    --backdrop: #d7d8d9;
    --card: #ffffff;
    --teal: #7fcdc1;
    --red: #e5202b;
    --ink: #1f1f24;
    --on-teal: #ffffff;
    --card-shadow: rgba(0, 0, 0, 0.18);
  }
  * { margin: 0; padding: 0; box-sizing: border-box; }
  html, body {
    width: 1200px;
    height: 771px;
    overflow: hidden;
    background: var(--backdrop);
  }
  .stage {
    position: relative;
    width: 1200px;
    height: 771px;
    display: flex;
    align-items: center;
    justify-content: center;
    gap: 40px;
  }
  .card {
    width: 530px;
    height: 303px;
    border-radius: 16px;
    background: var(--card);
    box-shadow: 0 6px 18px var(--card-shadow);
    overflow: hidden;
  }
  .card svg { display: block; width: 530px; height: 303px; }
  .brand-name {
    font-family: "Michroma", sans-serif;
    font-size: 21px;
    fill: var(--ink);
  }
  .brand-name--small { font-size: 12px; }
  .brand-dot { fill: var(--red); }
  .band { fill: var(--teal); }
  .swoosh { fill: var(--red); }
  .contact-line {
    font-family: "Michroma", sans-serif;
    font-size: 9px;
    letter-spacing: 0.6px;
    fill: var(--on-teal);
  }
  .contact-icon { fill: var(--on-teal); }
  .contact-glyph { fill: none; stroke: var(--teal); stroke-width: 1.1; stroke-linecap: round; stroke-linejoin: round; }
  .holder-name {
    font-family: "Michroma", sans-serif;
    font-size: 15px;
    letter-spacing: 1.5px;
    fill: var(--on-teal);
  }
  .holder-title {
    font-family: "Michroma", sans-serif;
    font-size: 10px;
    letter-spacing: 1.5px;
    fill: var(--on-teal);
  }
</style>
</head>
<body>
<main class="stage">

  <!-- Front: brand mark -->
  <section class="card card--front" aria-label="Business card front">
    <svg viewBox="0 0 530 303" xmlns="http://www.w3.org/2000/svg">
      <circle class="brand-dot" cx="112" cy="151" r="13"/>
      <text class="brand-name" x="138" y="159">The Gilded Ladle</text>
    </svg>
  </section>

  <!-- Back: contact details -->
  <section class="card card--back" aria-label="Business card back">
    <svg viewBox="0 0 530 303" xmlns="http://www.w3.org/2000/svg">
      <path class="band" d="M0,100 C170,96 330,150 530,218 L530,303 L0,303 Z"/>
      <path class="swoosh" d="M40,82 C210,70 360,118 470,200 C360,132 210,88 40,88 Z"/>

      <g class="brand-lockup">
        <circle class="brand-dot" cx="212" cy="40" r="8"/>
        <text class="brand-name brand-name--small" x="228" y="45">The Gilded Ladle</text>
      </g>

      <g class="contact-list">
        <g class="contact-item">
          <circle class="contact-icon" cx="36" cy="130" r="6"/>
          <path class="contact-glyph" d="M36,133.5 C34,131 33,130 33,128.8 A3,3 0 0 1 39,128.8 C39,130 38,131 36,133.5 Z"/>
          <text class="contact-line" x="48" y="133">Suite 210, Orchard Hall</text>
          <text class="contact-line" x="48" y="147">Portland, OR 97205</text>
        </g>
        <g class="contact-item">
          <circle class="contact-icon" cx="36" cy="164" r="6"/>
          <path class="contact-glyph" d="M33.5,161.5 L35,161 L36,163 L35.2,163.8 C35.8,165 36.5,165.7 37.2,166.2 L38,165.4 L40,166.4 L39.5,168 C36,168 33.5,165 33.5,161.5 Z"/>
          <text class="contact-line" x="48" y="167">503-555-0142</text>
          <text class="contact-line" x="48" y="181">503-555-0187</text>
        </g>
        <g class="contact-item">
          <circle class="contact-icon" cx="36" cy="198" r="6"/>
          <path class="contact-glyph" d="M32.8,195.8 H39.2 V200.2 H32.8 Z M32.8,195.8 L36,198.4 L39.2,195.8"/>
          <text class="contact-line" x="48" y="201">hello@gildedladle.com</text>
        </g>
        <g class="contact-item">
          <circle class="contact-icon" cx="36" cy="216" r="6"/>
          <path class="contact-glyph" d="M32.8,216 H39.2 M36,212.8 C34,215 34,217 36,219.2 C38,217 38,215 36,212.8"/>
          <text class="contact-line" x="48" y="219">www.gildedladle.com</text>
        </g>
      </g>

      <text class="holder-name" x="500" y="262" text-anchor="end">MARA ELLISON</text>
      <text class="holder-title" x="500" y="279" text-anchor="end">OWNER / C.E.O</text>
    </svg>
  </section>

</main>
</body>
</html>
```